Create modern and sleek business card for luxury real estate company

We're a "boutique" real estate office looking for a design that gets across a highly modern luxury brand. Blacks and whites are probably the best colors unless we try a silver foil for the logo. I've attached a version of our current logo here. I'd like to swap out the current font on there with Gotham Light Regular.

I'm looking to have one side of the card have the logo with the space for our agents info on the other side.

Target Market(s)

Young professionals in a "luxury" headspace

Industry/Entity Type

Real estate

Contact Information for Business Card

A place for agent name, cell number, website. The slogan "Quietly Redefining Fine Living".

Font styles to use
Other font styles liked:
• Gotham Regular

Colors

Designer to choose only greyscale colors for use in the design.

Requirements
Must have
• Matte black as the background color. Clean lines and use of contrast. A specific design aspect that will use silver foil.
Nice to have
• Up in the air on integrating a QR code
Should not have
• Any houses or other real estate related design (ex: a clip art house)

```html
<!DOCTYPE html>
<html lang="en">
<head>
<meta charset="utf-8">
<title>Vantage Realty — Business Card</title>
<link href="https://fonts.googleapis.com/css2?family=Montserrat:wght@300;400;600&family=Open+Sans:wght@400&display=swap" rel="stylesheet">
<style>
  :root {
    --stage: #3b3b3b;
    --card: #0d0d0d;
    --foil: #e6e6e6;
    --muted: #8a8a8a;
    --rule: #5a5a5a;
    --gloss-a: #151515;
    --gloss-b: #232323;
  }
  * { box-sizing: border-box; margin: 0; padding: 0; }
  html, body { width: 1200px; height: 801px; overflow: hidden; }
  body {
    background: var(--stage);
    display: flex;
    align-items: center;
    justify-content: center;
    gap: 40px;
    font-family: "Montserrat", sans-serif;
  }
  .card {
    position: relative;
    width: 520px;
    height: 297px;
    background: var(--card);
    color: var(--foil);
  }
  /* Front */
  .brand {
    position: absolute;
    left: 36px;
    top: 40px;
    display: flex;
    align-items: center;
    gap: 14px;
  }
  .brand-circle {
    width: 46px; height: 46px;
    border: 2px solid var(--foil);
    border-radius: 50%;
  }
  .brand-name {
    font-weight: 400;
    font-size: 20px;
    letter-spacing: 3px;
    line-height: 1.15;
    text-transform: uppercase;
  }
  .agent {
    position: absolute;
    right: 36px;
    top: 40px;
    text-align: right;
  }
  .agent-name {
    font-weight: 600;
    font-size: 17px;
    letter-spacing: 1px;
    text-transform: uppercase;
  }
  .agent-title {
    font-family: "Open Sans", sans-serif;
    font-size: 11px;
    color: var(--muted);
    margin-top: 3px;
  }
  .agent-rule {
    position: absolute;
    right: 36px;
    top: 100px;
    width: 250px;
    border-top: 1px solid var(--rule);
  }
  .contact-rule {
    position: absolute;
    left: 36px;
    bottom: 92px;
    width: 250px;
    border-top: 1px solid var(--rule);
  }
  .contact {
    position: absolute;
    left: 36px;
    bottom: 26px;
    list-style: none;
    font-family: "Open Sans", sans-serif;
    font-size: 12px;
    line-height: 20px;
  }
  .contact li { display: flex; align-items: center; gap: 9px; }
  .contact svg { width: 10px; height: 10px; fill: var(--foil); }
  /* Back */
  .gloss-field {
    position: absolute;
    inset: 0;
    background: linear-gradient(120deg, var(--gloss-a) 0%, var(--gloss-b) 55%, var(--gloss-a) 100%);
  }
  .back-mark {
    position: absolute;
    right: 40px;
    top: 118px;
    display: flex;
    align-items: center;
    gap: 12px;
  }
  .back-circle {
    width: 44px; height: 44px;
    border: 2px solid var(--foil);
    border-radius: 50%;
  }
  .back-name {
    font-size: 14px;
    letter-spacing: 2px;
    text-transform: uppercase;
  }
  .slogan {
    position: absolute;
    left: 0; right: 0;
    bottom: 56px;
    text-align: center;
    font-weight: 300;
    font-size: 14px;
    letter-spacing: 1.5px;
    text-transform: uppercase;
  }
</style>
</head>
<body>
  <section class="card card-front">
    <div class="brand">
      <span class="brand-circle"></span>
      <span class="brand-name">Vantage<br>Realty</span>
    </div>
    <div class="agent">
      <div class="agent-name">Daniel Hale</div>
      <div class="agent-title">President</div>
    </div>
    <div class="agent-rule"></div>
    <div class="contact-rule"></div>
    <ul class="contact">
      <li><svg viewBox="0 0 10 10"><path d="M2 0.5 L4 2.8 L3 4 Q4.5 6 6 7 L7.2 6 L9.5 8 L8 9.6 Q3.5 9 0.4 2 Z"/></svg>555-010-4821</li>
      <li><svg viewBox="0 0 10 10"><path d="M0 2 H10 V8 H0 Z M0.8 2.6 L5 5.6 L9.2 2.6" stroke="#0d0d0d" stroke-width="0.8"/></svg>dhale@vantagerealty.com</li>
      <li><svg viewBox="0 0 10 10"><circle cx="5" cy="5" r="4.6"/></svg>www.vantagerealty.com</li>
    </ul>
  </section>

  <section class="card card-back">
    <div class="gloss-field" role="img" aria-label="Repeating gloss-varnish monogram pattern across the card"></div>
    <div class="back-mark">
      <span class="back-circle"></span>
      <span class="back-name">Vantage Realty</span>
    </div>
    <p class="slogan">Quietly Redefining Fine Living</p>
  </section>
</body>
</html>
```